A website where experts collaborate on your project

I am building a new website where experts (yes, like designers) collaborate on projects with the project owner. More minds = more collaboration = better end product. Please see Pelmora(dot)com for a quick landing page I created for collaborating on presentations (although there will be many project types offered)

I am looking for a DESIGNER LONG TERM, but for now, just need initial mock ups to show the web programmers.

I have 21 Word documents loosely designed, what I would like to see here is a theme. Please DO NOT GO OFF WHAT YOU CURRENTLY SEE AT PELMORA. What is up now is only a quick landing page.

You can view a Word doc of the homepage here:
https://www.filevanta.com/s/qx83kdm2/home.docx?dl=0

WHAT AM I LOOKING FOR?
A clean, well designed theme.

Here is a link to the logo:
https://www.filevanta.com/s/mr47tpz9/logo%20-%20horizontal.tif?dl=0
-----------------------------------------
Here are a few sites I like the design of and what I like about them:
www.quenbrook.com-all around my favorite, beautiful graphics, clean layout, bold use of colors on a dark background
Ravelto.com- clean layout, The use of humans and bubble style elements.
Mintharbor.com :) clean, bold, unique pop art style but professional
plumevault.com - From the unique colors and artwork and the ability of that art to not interfere with the important elements of the site
sparkwidgets.com-clean, nice colors, well organized and separated sections.
www.dunmereco.com-love the font, use of colors and sectionalized style

All in all, I am not picky and open to so many styles. I would ultimately like the designer I pick to design all 21 pages.
Updates

Hello everyone,Moving forward, I would like you all to pay special attention to the section in my brief titled "Here are a few sites I like the design of and what I like about them". Please see below, I handpicked each one of these as sites I really like. Thank you.Here are a few sites I like the design of and what I like about them:Ravelto.com- clean layout, The use of humans and bubble style elements.Mintharbor.com :) clean, bold, unique pop art style but professionalwriteraccess.com - From the unique colors and artwork and the ability of that art to not interfere with the important elements of the sitegrowthgeeks.com-clean, nice colors, well organized and separated sections.www.dunmereco.com-love the font, use of colors and sectionalized stylewww.quenbrook.com-beautiful graphics, clean layout, bold use of colors----------------------------------------- Added Tuesday, November 24, 2015

I updated the homepage, you can see it here:https://www.dropbox.com/s/kwlkbsookq3cg2m/1new%20homepage.docx?dl=0I am modeling it after my favorite designed site: triplelift.comI love the dark colors with the orange glowing style boldness of the buttons. It's real clean too. Added Tuesday, November 24, 2015

Target Market(s)

small business owners, marketers, freelancer writers, graphic designers,

Industry/Entity Type

Building

Number of Pages Required

5+ page

Requirements
Must have
• I can't think of anything the project must have.
Nice to have
• WHAT AM I LOOKING FOR?
• A clean, well designed theme. I had a designer do a bit of work putting elements together, I found it to be very plain, but I like the Application Page (https://www.filevanta.com/s/jb19ckr3/Pelmora-Website.ai?dl=0)
• Here is a link to the logo:
• https://www.filevanta.com/s/mr47tpz9/logo%20-%20horizontal.tif?dl=0
• Here are a few sites I like the design of and what I like about them:
• Ravelto.com- clean layout, The use of humans and bubble style elements.
• Mintharbor.com :) clean, bold, unique pop art style but professional
• plumevault.com - From the unique colors and artwork and the ability of that art to not interfere with the important elements of the site
• sparkwidgets.com-clean, nice colors, well organized and separated sections.
• www.dunmereco.com-love the font, use of colors and sectionalized style
• www.quenbrook.com-beautiful graphics, clean layout, bold use of colors
• -----------------------------------------
Should not have
• out of the boxed, templated style website. I want this site to be memorable and not look like a thousand others

```html
<!DOCTYPE html>
<html lang="en">
<head>
<meta charset="utf-8">
<title>Pelmora – Experts collaborating on your project</title>
<link rel="stylesheet" href="https://fonts.googleapis.com/css2?family=Open+Sans:ital,wght@0,400;0,600;0,700;1,600&display=swap">
<style>
:root{
  --orange:#f7931e;
  --orange-light:#fbb040;
  --orange-deep:#ef7f1a;
  --teal:#3aa3c4;
  --teal-band:#4ab0cf;
  --ink:#555;
  --muted:#888;
  --line:#e6e6e6;
  --panel:#f5f5f5;
  --footer:#3a3a3a;
}
*{box-sizing:border-box;margin:0;padding:0}
html,body{width:677px;height:1200px;overflow:hidden}
body{position:relative;background:#fff;font-family:"Open Sans",Arial,sans-serif;color:var(--ink);font-size:8px}
.abs{position:absolute}

/* header */
.topline{left:0;top:0;width:677px;height:2px;background:var(--orange)}
.brand{left:55px;top:26px;display:flex;align-items:center;gap:6px;font-size:15px;font-weight:600;color:var(--orange)}
.brand-dot{width:22px;height:22px;border-radius:50%;background:var(--orange)}
.menu-toggle{left:604px;top:22px;width:16px}
.menu-toggle span{display:block;height:3px;background:var(--orange);border-radius:2px;margin-bottom:3px}

.navbar{left:0;top:55px;width:677px;height:39px;background:linear-gradient(#fbb040,#f7931e)}
.browse{left:55px;top:65px;width:167px;height:19px;background:#fff;border-radius:2px;font-size:7px;color:var(--muted);padding:5px 10px}
.browse svg{position:absolute;right:12px;top:6px}
.bell{left:315px;top:66px}
.nav-links{left:359px;top:71px;display:flex;font-size:7.5px;font-weight:600;color:#fff}
.nav-links li{list-style:none;margin-right:32px;white-space:nowrap}

/* hero */
.hero{left:0;top:94px;width:677px;height:268px;background:linear-gradient(90deg,#eef2f4 0%,#d9e3ea 38%,#8fb0cc 62%,#4d6f95 100%)}
.hero-title{left:53px;top:176px;font-size:19px;font-weight:700;color:var(--orange-light)}
.hero-sub{left:53px;top:206px;font-size:13.5px;font-style:italic;font-weight:600;color:var(--teal);line-height:19px}
.cta{left:54px;top:257px;width:121px;height:27px;background:linear-gradient(#fbb040,#f7931e);color:#fff;font-size:13.5px;font-style:italic;font-weight:600;text-align:center;line-height:27px}
.dots{left:326px;top:345px;display:flex;gap:4px}
.dots i{width:5px;height:5px;border-radius:50%;background:#fff;opacity:.7}
.dots i:nth-child(2){background:var(--teal)}

/* filters */
.filters-btn{left:57px;top:404px;width:151px;height:24px;background:linear-gradient(#fbb040,#f7931e);border-radius:2px;color:#fff;font-size:11px;font-weight:600;padding:5px 13px}
.filters-btn svg{position:absolute;right:12px;top:9px}
.label-teal{color:var(--teal);font-weight:600;font-size:8.5px}
.opt{font-size:6.5px;color:var(--ink);display:flex;align-items:center;gap:6px}
.opt i{width:7px;height:6px;border:1px solid var(--orange);border-radius:50% 50% 50% 0}
.range{left:59px;top:530px;display:flex;align-items:center;gap:5px;color:var(--orange);font-size:7px}
.range .field{width:37px;height:14px;background:#f3f3f3}
.go{width:22px;height:13px;background:var(--orange);color:#fff;font-size:6.5px;text-align:center;line-height:13px;border-radius:1px}
.acc-head{left:56px;top:564px;width:158px;height:29px;background:#f2f2f2;font-size:9px;color:var(--teal);padding:8px 14px}
.country-list{left:73px;top:605px;font-size:7.5px;color:#444;font-weight:600;list-style:none}
.country-list li{height:21px}
.acc-row{left:56px;width:158px;height:30px;border-bottom:1px solid var(--line);font-size:9px;color:var(--teal);padding:8px 14px}
.acc-row svg{position:absolute;right:14px;top:13px}
.status{display:flex;gap:38px}
.status span{display:flex;align-items:center;gap:4px}
.status .r{width:8px;height:8px;border:1px solid #999;border-radius:50%}
.status .on{border-color:var(--orange);background:radial-gradient(var(--orange) 40%,#fff 45%)}
.status .off{color:#999}
.save{left:57px;top:897px;width:155px;height:24px;background:linear-gradient(#fbb040,#f7931e);color:#fff;font-size:7.5px;font-weight:600;text-align:center;line-height:24px}

/* timeline */
.timeline{left:233px;top:404px;width:1px;height:512px;background:#ececec}
.node{width:10px;height:10px;border-radius:50%;border:1px solid #f0d9c0;background:#fff;left:229px}

/* projects */
.section-title{font-size:10.5px;font-weight:600;color:var(--orange)}
.sort{font-size:7px;color:#666;display:flex;align-items:center}
.sort .tab{height:26px;line-height:26px;padding:0 10px;color:#666}
.sort .active{background:#efefef;color:var(--orange);border:1px solid #e4e4e4;border-bottom:none}
.crowded{left:258px;top:430px;width:366px;height:164px;background:#f4f4f4;border:1px solid #ececec}
.featured{left:258px;top:646px;width:366px;height:272px;border:1px solid #ececec;background:#fff}
.meta{font-size:7px;font-weight:600;color:var(--orange);line-height:15px}
.meta b{color:var(--teal);font-weight:600}
.copy{font-size:6.8px;color:#888;line-height:12px}
.avatar{width:54px;height:60px}
.meta-row{font-size:7px;font-weight:600;color:var(--orange)}
.meta-row b{color:var(--teal);font-weight:600}
.rule{height:1px;background:var(--line)}

/* testimonials */
.testimonials{left:0;top:950px;width:677px;height:202px;background:linear-gradient(90deg,#3c9ec0,#5cb7d3 50%,#3c9ec0)}
.t-title{left:0;top:975px;width:677px;text-align:center;color:#fff;font-size:11.5px}
.t-card{left:56px;top:1016px;width:565px;height:104px;background:rgba(255,255,255,.14)}
.quote{left:100px;top:1042px;width:460px;color:#fff;font-size:11px;line-height:21px}
.person{right:190px;top:1080px;color:#fff;text-align:right;white-space:nowrap}
.person .name{font-size:10.5px;line-height:13px}
.person .role{font-size:7px;font-style:italic;font-weight:600;line-height:11px}
.t-avatar{left:503px;top:1069px;width:40px;height:40px;border-radius:50%;border:2px solid #fff;background:linear-gradient(#c9d4dc,#8fa3b3)}
.arrow{top:1062px}

/* footer */
.footer{left:0;top:1152px;width:677px;height:48px;background:var(--footer)}
.social{top:1166px;width:22px;height:22px;background:#5b5b5b}
.legal{right:57px;top:1172px;color:#fff;font-size:6.5px}
.code{left:638px;top:1171px;color:#fff;font-size:7.5px}
</style>
</head>
<body>

<header>
  <div class="abs topline"></div>
  <div class="abs brand"><span>pelmora</span><span class="brand-dot"></span></div>
  <div class="abs menu-toggle"><span></span><span></span><span></span></div>
</header>

<nav>
  <div class="abs navbar"></div>
  <div class="abs browse">BROWSE BY
    <svg width="8" height="6"><path d="M0 0h8L4 6z" fill="#f7931e"/></svg>
  </div>
  <svg class="abs bell" width="16" height="18" viewBox="0 0 16 18">
    <path d="M3 14V8a5 5 0 0 1 10 0v6z" fill="#3aa3c4"/>
    <circle cx="12" cy="4" r="3.5" fill="#3aa3c4" stroke="#fff"/>
  </svg>
  <ul class="abs nav-links">
    <li>PROJECTS</li><li>HOW IT WORKS</li><li>PLANS ▾</li><li>MY ACCOUNT</li>
  </ul>
</nav>

<section>
  <div class="abs hero" role="img" aria-label="Photo of two smiling colleagues discussing work in an office"></div>
  <h1 class="abs hero-title">CONVERT MORE CUSTOMERS</h1>
  <p class="abs hero-sub">Experience the power of experts<br>collaborating on</p>
  <div class="abs cta">Get Started</div>
  <div class="abs dots"><i></i><i></i><i></i></div>
</section>

<aside>
  <div class="abs filters-btn">FILTERS
    <svg width="7" height="5"><path d="M0 0h7L3.5 5z" fill="#fff"/></svg>
  </div>
  <div class="abs label-teal" style="left:58px;top:440px">PRICE</div>
  <div class="abs opt" style="left:58px;top:462px"><i></i>UNDER $20</div>
  <div class="abs opt" style="left:127px;top:462px"><i></i>ABOVE $1000</div>
  <div class="abs opt" style="left:58px;top:480px"><i></i>FROM $100</div>
  <div class="abs opt" style="left:127px;top:480px"><i></i>TO $ 200</div>
  <div class="abs opt" style="left:58px;top:495px"><i></i>FROM $200</div>
  <div class="abs opt" style="left:127px;top:495px"><i></i>TO $ 500</div>
  <div class="abs opt" style="left:58px;top:510px"><i></i>FROM $500</div>
  <div class="abs opt" style="left:127px;top:510px"><i></i>TO $ 1000</div>
  <div class="abs range"><span>$</span><span class="field"></span><span>- $</span><span class="field"></span><span class="go">GO</span></div>

  <div class="abs acc-head">Country
    <svg class="abs" style="right:14px;top:13px" width="6" height="4"><path d="M0 4l3-3 3 3" fill="none" stroke="#999"/></svg>
  </div>
  <ul class="abs country-list"><li>India</li><li>America</li><li>Australia</li><li>Africa</li><li>France</li></ul>

  <div class="abs acc-row" style="top:712px">Categories<svg width="6" height="4"><path d="M0 0l3 3 3-3" fill="none" stroke="#999"/></svg></div>
  <div class="abs acc-row" style="top:742px">Time Left<svg width="6" height="4"><path d="M0 0l3 3 3-3" fill="none" stroke="#999"/></svg></div>
  <div class="abs acc-row" style="top:772px"><div class="status"><span><i class="r on"></i>Active</span><span class="off"><i class="r"></i>Expired</span></div></div>
  <div class="abs acc-row" style="top:802px">Contains adult content<svg width="6" height="4"><path d="M0 0l3 3 3-3" fill="none" stroke="#999"/></svg></div>
  <div class="abs acc-row" style="top:832px">keywords<svg width="6" height="4"><path d="M0 0l3 3 3-3" fill="none" stroke="#999"/></svg></div>
  <div class="abs acc-row" style="top:862px;border:none">Followers<svg width="6" height="4"><path d="M0 0l3 3 3-3" fill="none" stroke="#999"/></svg></div>
  <div class="abs save">SAVE FILTER</div>
</aside>

<div class="abs timeline"></div>
<div class="abs node" style="top:404px"></div>
<div class="abs node" style="top:531px"></div>
<div class="abs node" style="top:650px"></div>
<div class="abs node" style="top:772px"></div>
<div class="abs node" style="top:910px"></div>

<main>
  <h2 class="abs section-title" style="left:258px;top:409px">CROWDED PROJECTS</h2>
  <div class="abs sort" style="left:411px;top:404px">Sort :&nbsp;&nbsp;&nbsp;<span class="tab active">Price</span><span class="tab">country</span><span class="tab">Time left</span></div>
  <div class="abs crowded"></div>

  <svg class="abs avatar" style="left:273px;top:453px" viewBox="0 0 54 60" role="img" aria-label="Expert profile photo">
    <path d="M27 2a25 25 0 1 1-12 47L46 58 38 46A25 25 0 0 1 27 2z" fill="#f7931e"/>
    <circle cx="27" cy="27" r="22" fill="#c8b7a8"/>
  </svg>
  <div class="abs meta" style="left:348px;top:469px">TIME LEFT&nbsp; : &nbsp;<b>6 DAYS</b><br>PRICE&nbsp;&nbsp;&nbsp;&nbsp;&nbsp;&nbsp;&nbsp;: &nbsp;<b>$ 80</b><br>COUNTRY&nbsp; : &nbsp;<b>UK</b></div>
  <p class="abs copy" style="left:272px;top:526px;width:160px">Morbi in ante arcu. Maecenas sit amet sem vel His epicurei menandri salutandi ad.antas labore quo an, eum iisque adolescens.</p>
  <div class="abs" style="left:442px;top:458px;width:1px;height:108px;background:#e2e2e2"></div>
  <p class="abs copy" style="left:455px;top:458px;width:156px;text-align:right">Morbi in ante arcu. Maecenas sit amet sem vel His epicurei menandri salutandi ad.antas labore quo an, eum iisque adolescens.</p>
  <div class="abs meta" style="left:459px;top:510px">TIME LEFT&nbsp; : &nbsp;<b>6 DAYS</b><br>PRICE&nbsp;&nbsp;&nbsp;&nbsp;&nbsp;&nbsp;&nbsp;: &nbsp;<b>$ 50</b><br>COUNTRY&nbsp; : &nbsp;<b>UK</b></div>
  <svg class="abs" style="left:546px;top:512px" width="68" height="54" viewBox="0 0 68 54" role="img" aria-label="Expert profile photo">
    <path d="M42 2a25 25 0 1 1-14 45L2 40l15-3A25 25 0 0 1 42 2z" fill="#f7931e"/>
    <circle cx="42" cy="27" r="22" fill="#b9aea4"/>
  </svg>

  <h2 class="abs section-title" style="left:257px;top:625px">FEATURED PROJECTS</h2>
  <div class="abs sort" style="left:410px;top:620px">Sort :&nbsp;&nbsp;&nbsp;<span class="tab active">Price</span><span class="tab">country</span><span class="tab">Time left</span></div>
  <div class="abs featured"></div>

  <svg class="abs avatar" style="left:265px;top:665px" viewBox="0 0 54 60" role="img" aria-label="Expert profile photo">
    <path d="M27 2a25 25 0 1 1-12 47L46 58 38 46A25 25 0 0 1 27 2z" fill="#f7931e"/>
    <circle cx="27" cy="27" r="22" fill="#cdbfb3"/>
  </svg>
  <p class="abs copy" style="left:335px;top:668px;width:282px">Morbi in ante arcu. Maecenas sit amet sem vel His epicurei menandri salutandi ad.antas labore quo an, eum iisque adolescens.</p>
  <div class="abs meta-row" style="left:335px;top:702px">TIME LEFT&nbsp; : &nbsp;<b>6 DAYS</b></div>
  <div class="abs meta-row" style="left:435px;top:702px">PRICE</div>
  <div class="abs meta-row" style="left:470px;top:702px">: &nbsp;<b>$ 80</b></div>
  <div class="abs meta-row" style="left:526px;top:702px">COUNTRY&nbsp; : &nbsp;<b>UK</b></div>
  <div class="abs rule" style="left:335px;top:737px;width:280px"></div>

  <svg class="abs avatar" style="left:265px;top:755px" viewBox="0 0 54 60" role="img" aria-label="Expert profile photo">
    <path d="M27 2a25 25 0 1 1-12 47L46 58 38 46A25 25 0 0 1 27 2z" fill="#f7931e"/>
    <circle cx="27" cy="27" r="22" fill="#8a8f98"/>
  </svg>
  <p class="abs copy" style="left:335px;top:758px;width:282px">Morbi in ante arcu. Maecenas sit amet sem vel His epicurei menandri salutandi ad.antas labore quo an, eum iisque adolescens.</p>
  <div class="abs meta-row" style="left:335px;top:792px">TIME LEFT&nbsp; : &nbsp;<b>6 DAYS</b></div>
  <div class="abs meta-row" style="left:435px;top:792px">PRICE</div>
  <div class="abs meta-row" style="left:470px;top:792px">: &nbsp;<b>$ 80</b></div>
  <div class="abs meta-row" style="left:526px;top:792px">COUNTRY&nbsp; : &nbsp;<b>UK</b></div>
  <div class="abs rule" style="left:335px;top:828px;width:280px"></div>

  <svg class="abs avatar" style="left:265px;top:846px" viewBox="0 0 54 60" role="img" aria-label="Expert profile photo">
    <path d="M27 2a25 25 0 1 1-12 47L46 58 38 46A25 25 0 0 1 27 2z" fill="#f7931e"/>
    <circle cx="27" cy="27" r="22" fill="#b8bcc2"/>
  </svg>
  <p class="abs copy" style="left:335px;top:849px;width:282px">Morbi in ante arcu. Maecenas sit amet sem vel His epicurei menandri salutandi ad.antas labore quo an, eum iisque adolescens.</p>
  <div class="abs meta-row" style="left:335px;top:883px">TIME LEFT&nbsp; : &nbsp;<b>6 DAYS</b></div>
  <div class="abs meta-row" style="left:435px;top:883px">PRICE</div>
  <div class="abs meta-row" style="left:470px;top:883px">: &nbsp;<b>$ 80</b></div>
  <div class="abs meta-row" style="left:526px;top:883px">COUNTRY&nbsp; : &nbsp;<b>UK</b></div>
</main>

<section>
  <div class="abs testimonials" role="img" aria-label="Blue-tinted photo of people walking in a glass office lobby"></div>
  <h2 class="abs t-title" style="font-weight:400">CLIENT TESTIMONIALS</h2>
  <div class="abs t-card"></div>
  <p class="abs quote">“With Pelmora I have multiple experts perfecting my content and I only pay for the feedback I find valuable. It’s perfect”</p>
  <div class="abs person"><div class="name">OWEN MARLOW</div><div class="role">CEO , Ridge 40</div></div>
  <div class="abs t-avatar" role="img" aria-label="Client portrait"></div>
  <svg class="abs arrow" style="left:27px" width="8" height="14"><path d="M7 1L1 7l6 6" fill="none" stroke="#fff" stroke-width="2"/></svg>
  <svg class="abs arrow" style="left:642px" width="8" height="14"><path d="M1 1l6 6-6 6" fill="none" stroke="#fff" stroke-width="2"/></svg>
</section>

<footer>
  <div class="abs footer"></div>
  <div class="abs social" style="left:55px"></div>
  <div class="abs social" style="left:90px"></div>
  <div class="abs social" style="left:124px"></div>
  <div class="abs social" style="left:158px"></div>
  <div class="abs legal">All Rights Reserved . copyrights2015@pelmora.com</div>
  <div class="abs code">C18</div>
</footer>

</body>
</html>
```